web hosting reseller site, E-COMMERCE FUNCTIONALITY, AND MONTHLY PAYMENT INTERGRATION

hie there , i need a web hosting reseller site , 5 pages seo friendly , responsive and mobile friendly, i have a seller domain , basic content uploaded , design theme . i will be selling web hosting packages and domain names , i will also offer web design services and development . my project is so simple , the basic pages have content submitted already ,etc HOME, ABOUT, CONTACT US, BLOG POST .
Target Market(s)
5
Industry/Entity Type
web hosting
Coding
Coded - Design and coding required
Number of Pages Required
5+ page
Font styles to use
Requirements
Must have
- e commerce functionality, blog post, knowledge base , faq ,
Should not have
- affiliate links , subscription plugins

```html
<!DOCTYPE html>
<html lang="en">
<head>
<meta charset="utf-8">
<title>NimbusNest – Blogs</title>
<link href="https://fonts.googleapis.com/css2?family=Poppins:wght@400;500;600;700&family=Tinos:wght@700&display=swap" rel="stylesheet">
<style>
:root{
  --topbar:#c8e8f8;
  --blue:#0a8fd6;
  --hero:#26164f;
  --card:#f3f3f3;
  --ink:#222;
  --title:#333;
  --foot-left:#07a4e4;
  --foot-right:#0196d9;
  --white:#fff;
}
*{margin:0;padding:0;box-sizing:border-box}
html,body{width:1200px;height:3001px;overflow:hidden;background:var(--white);font-family:'Poppins',sans-serif;color:var(--ink)}
a{text-decoration:none;color:inherit}
.abs{position:absolute}
.topbar{position:absolute;left:0;top:0;width:1200px;height:58px;background:var(--topbar);font-size:16px;color:#1e2a3a}
.topbar .phone{position:absolute;left:75px;top:16px;color:var(--blue);font-weight:600;font-size:19px;display:flex;align-items:center;gap:6px}
.topbar .links{position:absolute;right:73px;top:18px;display:flex;gap:9px;align-items:center}
.topbar .links span{display:flex;align-items:center;gap:6px}
.nav{position:absolute;left:0;top:58px;width:1200px;height:109px;background:var(--white)}
.brand{position:absolute;left:75px;top:30px;display:flex;align-items:center;gap:8px;font-family:'Tinos',serif;font-weight:700;font-size:26px;color:#111}
.brand i{width:22px;height:22px;border-radius:50%;background:#111;display:block}
.menu{position:absolute;right:73px;top:46px;display:flex;gap:31px;font-family:'Tinos',serif;font-weight:700;font-size:18px;color:#111}
.menu .on{color:var(--blue)}
.hero{position:absolute;left:0;top:167px;width:1200px;height:511px;background:var(--hero)}
.hero-art{position:absolute;left:420px;top:0;width:780px;height:511px;background:radial-gradient(ellipse at 60% 55%,#5b3fc4 0%,#3a2891 35%,rgba(38,22,79,0) 70%),radial-gradient(circle at 80% 30%,#2fb6f0 0%,rgba(38,22,79,0) 30%)}
.hero h1{position:absolute;left:75px;top:218px;font-size:72px;font-weight:700;color:var(--white);letter-spacing:1px}
.img{position:absolute}
.date{font-size:16px;font-weight:600;color:var(--blue)}
.t-lg{font-family:'Tinos',serif;font-weight:700;font-size:37px;line-height:45px;color:var(--title);letter-spacing:1px;margin-top:12px}
.t-sm{font-family:'Tinos',serif;font-weight:700;font-size:26px;line-height:34px;color:var(--title);letter-spacing:1px;margin-top:8px}
.more{display:block;font-size:16px;color:var(--blue);margin-top:10px}
.card{position:absolute;background:var(--card);padding:26px 19px}
.card3{position:absolute;background:var(--card);width:329px;height:461px}
.card3 .body{padding:24px 18px}
.footer{position:absolute;left:0;top:2527px;width:1200px;height:474px;background:var(--foot-right)}
.footer .left{position:absolute;left:0;top:0;width:341px;height:474px;background:var(--foot-left);color:var(--white)}
.fbrand{position:absolute;left:77px;top:118px;display:flex;align-items:center;gap:8px;font-family:'Tinos',serif;font-weight:700;font-size:26px;color:#111}
.fbrand i{width:22px;height:22px;border-radius:50%;background:#111;display:block}
.copy{position:absolute;left:77px;top:198px;font-size:14px;line-height:26px}
.fphone{position:absolute;left:75px;top:265px;font-size:24px;font-weight:600;display:flex;gap:8px;align-items:center}
.social{position:absolute;left:77px;top:320px;display:flex;gap:24px}
.social span{width:22px;height:22px;border-radius:50%;background:var(--white);display:block}
.col{position:absolute;top:72px;color:var(--white)}
.col h3{font-family:'Tinos',serif;font-weight:700;font-size:23px;letter-spacing:1px;margin-bottom:8px}
.col li{list-style:none;font-size:15.5px;line-height:39.6px}
.col.svc li{line-height:32.3px}
</style>
</head>
<body>
<header class="topbar">
  <div class="phone"><svg width="14" height="16" viewBox="0 0 14 16"><path d="M3 1l3 3-2 2c1 2 3 4 5 5l2-2 3 3-2 3C6 15 0 8 1 3z" fill="#0a8fd6"/></svg>1-800-555-0142</div>
  <div class="links">
    <span><svg width="13" height="15"><rect x="1" y="6" width="11" height="8" fill="#0a8fd6"/><path d="M3 6V4a3.5 3.5 0 017 0v2" stroke="#0a8fd6" stroke-width="2" fill="none"/></svg>Log in</span><span>/</span>
    <span><svg width="18" height="14"><ellipse cx="8" cy="6" rx="7" ry="5" fill="#0a8fd6"/></svg>Live Chat</span><span>/</span>
    <span><svg width="12" height="14" viewBox="0 0 14 16"><path d="M3 1l3 3-2 2c1 2 3 4 5 5l2-2 3 3-2 3C6 15 0 8 1 3z" fill="#0a8fd6"/></svg>Call</span>
  </div>
</header>
<nav class="nav">
  <div class="brand"><i></i>NimbusNest</div>
  <div class="menu"><a>Home</a><a>About</a><a>Packages</a><a>Programs</a><a class="on">Blog</a><a>FAQ’s</a><a>Careers</a><a>Contact Us</a></div>
</nav>
<section class="hero">
  <div class="hero-art" role="img" aria-label="Isometric illustration of people working at a large laptop with server towers"></div>
  <h1>BLOGS</h1>
</section>

<main>
  <div class="img" style="left:75px;top:747px;width:512px;height:377px;background:linear-gradient(135deg,#dfe3e6,#3f7ec9 45%,#2c3440)" role="img" aria-label="Laptop on a desk showing a web hosting screen"></div>
  <div class="abs" style="left:75px;top:1148px;width:520px"><div class="date">Jun 20, 2022</div><div class="t-lg">Sed ut perspiciatis unde omnis iste natus error sit.</div></div>

  <div class="card" style="left:602px;top:747px;width:256px;height:255px"><div class="date">Jun 20, 2022</div><div class="t-sm">Sed ut perspiciatis unde omnis iste natusporroquis porro quisquam</div><a class="more">Learn More</a></div>
  <div class="card" style="left:870px;top:747px;width:257px;height:255px"><div class="date">Jun 20, 2022</div><div class="t-sm">Sed ut perspiciatis unde omnis iste natusporroquis porro quisquam</div><a class="more">Learn More</a></div>
  <div class="card" style="left:602px;top:1015px;width:256px;height:255px"><div class="date">Jun 20, 2022</div><div class="t-sm">Sed ut perspiciatis unde omnis iste natusporroquis porro quisquam</div><a class="more">Learn More</a></div>
  <div class="card" style="left:870px;top:1015px;width:257px;height:255px"><div class="date">Jun 20, 2022</div><div class="t-sm">Sed ut perspiciatis unde omnis iste natusporroquis porro quisquam</div><a class="more">Learn More</a></div>

  <div class="card3" style="left:75px;top:1339px"><div role="img" aria-label="Cloud network icons over a glowing server corridor" style="height:252px;background:linear-gradient(180deg,#0d3a57,#3fa3c9 60%,#d8f2fb)"></div><div class="body"><div class="date">Jun 20, 2022</div><div class="t-sm">Sed ut perspiciatis unde omnis iste natusporr oquis porro quisquam</div><a class="more">Learn More</a></div></div>
  <div class="card3" style="left:434px;top:1339px"><div role="img" aria-label="Technician with a laptop in a data center" style="height:252px;background:linear-gradient(90deg,#0f1a2b,#23344f 55%,#4a5b70)"></div><div class="body"><div class="date">Jun 20, 2022</div><div class="t-sm">Sed ut perspiciatis unde omnis iste natusporr oquis porro quisquam</div><a class="more">Learn More</a></div></div>
  <div class="card3" style="left:796px;top:1339px"><div role="img" aria-label="Code overlay on server racks" style="height:252px;background:linear-gradient(135deg,#17324a,#0b1621 55%,#3a2a3f)"></div><div class="body"><div class="date">Jun 20, 2022</div><div class="t-sm">Sed ut perspiciatis unde omnis iste natusporr oquis porro quisquam</div><a class="more">Learn More</a></div></div>

  <div class="img" style="left:75px;top:1859px;width:512px;height:377px;background:linear-gradient(180deg,#2c3fd8,#1f6fc4 55%,#e6e8ea)" role="img" aria-label="Magnifying glass over a website-builder homepage"></div>
  <div class="abs" style="left:75px;top:2260px;width:520px"><div class="date">Jun 20, 2022</div><div class="t-lg">Sed ut perspiciatis unde omnis iste natus error sit.</div></div>
  <div class="img" style="left:615px;top:1859px;width:512px;height:377px;background:linear-gradient(135deg,#f2f2f0,#c9ccc8 40%,#2f7d72 70%,#4a4c4e)" role="img" aria-label="Hands holding a tablet showing a hosting graphic"></div>
  <div class="abs" style="left:615px;top:2260px;width:520px"><div class="date">Jun 20, 2022</div><div class="t-lg">Sed ut perspiciatis unde omnis iste natus error sit.</div></div>
</main>

<footer class="footer">
  <div class="left">
    <div class="fbrand"><i></i>NimbusNest</div>
    <div class="copy">© Copyright 2022 CompanyName<br>All Rights Reserved</div>
    <div class="fphone"><svg width="16" height="18" viewBox="0 0 14 16"><path d="M3 1l3 3-2 2c1 2 3 4 5 5l2-2 3 3-2 3C6 15 0 8 1 3z" fill="#fff"/></svg>1-800-555-0142</div>
    <div class="social" aria-label="Social links"><span></span><span></span><span></span><span></span><span></span></div>
  </div>
  <div class="col" style="left:404px"><h3>Company</h3><ul><li>About</li><li>Careers</li><li>Contact</li><li>Terms Of Services</li><li>Privacy</li><li>Site Map</li><li>Blog</li><li>FAQ’s</li></ul></div>
  <div class="col svc" style="left:655px"><h3>Services</h3><ul><li>Web Hosting</li><li>SitePress Hosting</li><li>ShopCart Hosting</li><li>Reseller Hosting</li><li>Cloud Hosting</li><li>Domain Names</li><li>Dedicated hosting</li><li>Site Builder</li><li>SSL</li><li>Shared hosting</li></ul></div>
  <div class="col" style="left:925px"><h3>Programs</h3><ul><li>SitePress</li><li>Affiliate</li><li>Marketing services</li><li>SitePress guide</li></ul></div>
</footer>
</body>
</html>
```